Private Investment Firm Needs PowerPoint Presentation Template

Design PowerPoint template, take Pinebrook-submitted rough presentation draft, and drop it into new template. See attached Project Brief file for more detail.
Updates

Some decent designs have been submitted but they seem to lack the understanding of our target markets. I am hopeful that more time and feedback will result in better results.

Target Market(s)

Private company owners and intermediaries.

Font styles to use
Serif

Colors
3176b5

Requirements
Must have
• See attached Project Brief.
Nice to have
Should not have
• No B2C fluff--this is a B2B project.

```html
<!DOCTYPE html>
<html lang="en">
<head>
<meta charset="utf-8">
<title>What We Do / And Why — Pinebrook Capital</title>
<link rel="stylesheet" href="https://fonts.googleapis.com/css2?family=Montserrat:wght@500;600;700&family=Tinos&display=swap">
<style>
  :root {
    --brand-blue: #0a6dc1;
    --ink-grey: #555555;
    --white: #ffffff;
    --photo-light: #f7f9f9;
    --photo-mid: #dfe6e6;
  }
  * { margin: 0; padding: 0; box-sizing: border-box; }
  html, body { width: 1200px; height: 676px; overflow: hidden; background: var(--white); }
  .slide {
    position: relative;
    width: 1200px;
    height: 676px;
    background: var(--white);
    font-family: "Montserrat", sans-serif;
    overflow: hidden;
  }
  .side-rail {
    position: absolute; left: 0; top: 0;
    width: 44px; height: 676px;
    background: var(--brand-blue);
  }
  .side-rail__url {
    position: absolute;
    left: 22px; top: 337px;
    transform: translate(-50%, -50%) rotate(-90deg);
    white-space: nowrap;
    font-family: "Tinos", serif;
    font-size: 15px;
    color: var(--white);
    letter-spacing: 0.3px;
  }
  .edge-rail {
    position: absolute; right: 0; top: 0;
    width: 12px; height: 676px;
    background: var(--brand-blue);
  }
  .page-number {
    position: absolute; left: 1158px; top: 18px;
    font-family: "Tinos", serif;
    font-size: 20px;
    color: #222;
  }
  .slide-title {
    position: absolute; left: 86px; top: 80px;
    font-size: 29px; font-weight: 700;
    color: var(--brand-blue);
    letter-spacing: 0.4px;
  }
  .statement {
    position: absolute; right: 748px; top: 242px;
    text-align: right;
    font-size: 42px; font-weight: 600;
    line-height: 42.4px;
    color: var(--ink-grey);
  }
  .reasons {
    position: absolute; left: 482px; top: 170px;
    width: 706px; height: 334px;
    background: var(--brand-blue);
    list-style: none;
    padding: 20px 90px 0 62px;
  }
  .reasons__item {
    position: relative;
    padding-left: 0;
    font-size: 17.6px; font-weight: 500;
    line-height: 28px;
    color: var(--white);
    margin-bottom: 28px;
  }
  .reasons__item::before {
    content: "";
    position: absolute; left: -19px; top: 8px;
    width: 11px; height: 11px;
    border: 1.5px solid var(--white);
    background: rgba(255,255,255,0.25);
  }
  .reasons__item--single { margin-bottom: 28px; }
  .architecture-photo {
    position: absolute; left: 470px; top: 504px;
    width: 718px; height: 172px;
    background: linear-gradient(100deg, var(--white) 0%, var(--photo-light) 30%, var(--photo-mid) 70%, #cdd8d8 100%);
  }
  .brand {
    position: absolute; left: 67px; top: 616px;
    display: flex; align-items: center; gap: 10px;
  }
  .brand__mark {
    width: 30px; height: 30px; border-radius: 50%;
    background: var(--brand-blue);
  }
  .brand__name {
    font-size: 17px; font-weight: 600;
    color: var(--brand-blue);
    letter-spacing: 1px;
  }
</style>
</head>
<body>
<div class="slide">
  <div class="side-rail"><span class="side-rail__url">www.pinebrookcapital.com</span></div>
  <div class="edge-rail"></div>
  <div class="page-number">11</div>

  <h1 class="slide-title">WHAT WE DO / AND WHY</h1>

  <p class="statement">Non-Control<br>Capital<br>transactions<br>only</p>

  <ul class="reasons">
    <li class="reasons__item">Companies looking for a partner to help them grow, not sellers looking to exit</li>
    <li class="reasons__item">Management’s personal wealth directly tied to the performance of the investment</li>
    <li class="reasons__item reasons__item--single">Situational investors with a generalist approach</li>
    <li class="reasons__item">Our heritage reflects decades of Non-Control Capital invest­ing—it’s all we do</li>
  </ul>

  <div class="architecture-photo" role="img" aria-label="Photograph of a white modern building facade with curved vertical fins against a pale sky"></div>

  <div class="brand">
    <span class="brand__mark"></span>
    <span class="brand__name">PINEBROOK CAPITAL</span>
  </div>
</div>
</body>
</html>
```